Tech Savy small Business accountant business card design

We need a business card for a new company based in the cloud. We provide tax, business advisory, accounting, information technology solutions and back office functions to small businesses. We offer fixed fee packages with add on services as you need them. By harnessing technology we simplify small business operational processes providing valuable time and information for small business owners to grow their business. In the logo (bluvoria) we want to be able to see bluv and experts. The final design should communicate achieving growth dreams and balance (ie life and $).
Updates
This project has been temporarily placed on hold until I finalize "Tech Savy small Business accountant needs a logo". I invite all designers to submit on this logo project. Once my logo is finalized I will resume this business card contest. Thanks Added Wednesday, March 19, 2014
This project has been temporarily placed on hold until I finalize "Tech Savy small Business accountant logo". I invite all designers to submit on this logo project. Once my logo is finalized I will resume this business card contest. Thanks Added Thursday, March 20, 2014
Target Market(s)
Small Business (Revenue $500,000, more than 3 employees) owners.
Industry/Entity Type
Small Business
Contact Information for Business Card
Marcy Elwind (Principal)
Accountant, Tax Agent.
TEL | 0417 683 912
EMAIL | Marcy.Elwind@bluvoria.com.au
WEB | www.bluvoria.com.au
Look and feel

```html
<!DOCTYPE html>
<html lang="en">
<head>
<meta charset="utf-8">
<title>bluvoria business card</title>
<link href="https://fonts.googleapis.com/css2?family=Open+Sans:wght@400;600;700&display=swap" rel="stylesheet">
<style>
  :root {
    --brand-blue: #1a96d4;
    --brand-grey: #6d6e71;
    --text-grey: #58595b;
    --card-white: #ffffff;
    --backdrop: #e8e6e3;
  }
  * { margin: 0; padding: 0; box-sizing: border-box; }
  html, body {
    width: 1200px; height: 1000px; overflow: hidden;
    background: var(--backdrop);
    font-family: "Open Sans", Arial, sans-serif;
  }
  .stage { position: relative; width: 1200px; height: 1000px; }
  .card {
    position: absolute; left: 265px; width: 665px; height: 397px;
    border-radius: 22px; overflow: hidden;
    box-shadow: 0 4px 12px rgba(0,0,0,0.18);
  }
  .card-front { top: 73px; background: var(--card-white); }
  .card-back { top: 533px; background: var(--brand-grey); }

  .brand { position: absolute; left: 40px; top: 150px; }
  .brand-name {
    font-size: 50px; font-weight: 700; color: var(--brand-blue);
    line-height: 1; letter-spacing: -1px;
  }
  .brand-tagline {
    margin-top: 8px; font-size: 15px; color: var(--text-grey);
  }

  .holder { position: absolute; left: 368px; top: 114px; color: var(--text-grey); }
  .holder-name { font-size: 21px; font-weight: 700; color: var(--brand-blue); }
  .holder-role { font-size: 15.5px; line-height: 22px; }
  .holder-role-first { font-size: 15.5px; }

  .contacts { position: absolute; left: 368px; top: 201px; list-style: none; color: var(--text-grey); font-size: 15.5px; }
  .contacts li { display: flex; align-items: center; height: 24px; }
  .contacts svg { width: 14px; height: 14px; margin-right: 7px; fill: var(--brand-blue); }
  .contacts .web-domain { color: var(--brand-blue); }

  .band-blue {
    position: absolute; left: 0; top: 339px; width: 518px; height: 38px;
    background: var(--brand-blue);
  }
  .band-grey {
    position: absolute; left: 562px; top: 339px; width: 103px; height: 38px;
    background: var(--brand-grey);
  }
  .band-square {
    position: absolute; left: 529px; top: 347px; width: 22px; height: 22px;
    background: var(--brand-blue);
  }

  .back-name {
    position: absolute; left: 0; right: 0; top: 50%; transform: translateY(-50%);
    text-align: center; font-size: 54px; font-weight: 700; color: var(--card-white);
    letter-spacing: -1px;
  }
</style>
</head>
<body>
<main class="stage">
  <section class="card card-front" aria-label="Card front">
    <div class="brand">
      <div class="brand-name">bluvoria</div>
      <div class="brand-tagline">Your business and accounting partner</div>
    </div>

    <div class="holder">
      <div><span class="holder-name">Marcy Elwind</span> <span class="holder-role-first">/ Principal</span></div>
      <div class="holder-role">Accountant, Tax Agent</div>
    </div>

    <ul class="contacts">
      <li>
        <svg viewBox="0 0 16 16" aria-hidden="true"><path d="M1 5c0-2 3-3 7-3s7 1 7 3v1h-4V5c-1-.5-5-.5-6 0v1H1z"/><path d="M4 7h8l2 6H2z"/></svg>
        0417 683 912
      </li>
      <li>
        <svg viewBox="0 0 16 16" aria-hidden="true"><path d="M1 3h14v10H1z"/><path d="M1 3l7 6 7-6" fill="none" stroke="#fff" stroke-width="1.4"/></svg>
        Marcy.Elwind@bluvoria.com.au
      </li>
      <li>
        <svg viewBox="0 0 16 16" aria-hidden="true"><circle cx="8" cy="8" r="7"/><path d="M1 8h14M8 1v14M3 4h10M3 12h10" stroke="#fff" stroke-width="1" fill="none"/><ellipse cx="8" cy="8" rx="3" ry="7" fill="none" stroke="#fff" stroke-width="1"/></svg>
        <span>www.<span class="web-domain">bluvoria</span>.com.au</span>
      </li>
    </ul>

    <div class="band-blue"></div>
    <div class="band-square"></div>
    <div class="band-grey"></div>
  </section>

  <section class="card card-back" aria-label="Card back">
    <div class="back-name">bluvoria</div>
  </section>
</main>
</body>
</html>
```